New website for salon services and wedding hair and makeup

I am a professional hairstylist and makeup artist in Charleston, SC. I have my own company where I see clients for cut and color and I also go on site for weddings. I have a current website that I would like to update and change the style. I would like to add a contact form, map, additional pages and be mobile friendly. It is important to me that it have a site map and can show up in searches. I will need to add photos to the site every so often and would like to continue to work with the designer. I have a logo that I am happy with and have attached the file however if you think a new logo would help the look of the site I am open to it. My current website is www.brightcombstudio-example.com, I would like to change the style and layout so it looks up to date. Here are some links to sites that I like the look of but I don't want to limit your creativity. http://willowlanefolio-example.com/ http://www.runwaylensworks-example.com http://miraventhol-example.com/. I have attached a few files for mock up purposes, please let me know if you would like more content. Thank you!

Target Market(s)

Women, Brides

Industry/Entity Type

Hair And Beauty

Number of Pages Required

1 page

Font styles to use
Sans Serif
Script

Requirements
Must have
• Contact form, Mobile friendly, sitemap
Nice to have
• I really like the look for the sites I have included on the project description guide.
Should not have
• Nothing overly girly.

```html
<!DOCTYPE html>
<html lang="en">
<head>
<meta charset="utf-8">
<title>Brightcomb — Wedding Hair and Makeup</title>
<link rel="stylesheet" href="https://fonts.googleapis.com/css2?family=Open+Sans:wght@400;600;700&display=swap">
<style>
  :root {
    --navy: #0d3b66;
    --navy-light: #1d5a92;
    --accent: #1f6fb2;
    --ink: #2a2a2a;
    --muted: #666;
    --rule: #dcdcdc;
    --footer: #1e1e1e;
    --white: #fff;
  }
  * { box-sizing: border-box; margin: 0; padding: 0; }
  html, body { width: 898px; height: 1200px; overflow: hidden; background: var(--white); }
  body { font-family: "Open Sans", Arial, sans-serif; color: var(--ink); position: relative; }

  .site-header { position: relative; height: 111px; }
  .brand {
    position: absolute; left: 40px; top: 14px; height: 20px;
    display: flex; align-items: center;
    font-size: 15px; font-weight: 600; color: var(--navy); line-height: 20px;
  }
  .follow { position: absolute; right: 54px; top: 30px; text-align: left; }
  .follow-label { font-size: 8px; font-weight: 600; color: var(--ink); letter-spacing: .5px; margin-bottom: 5px; }
  .social { display: flex; gap: 4px; }
  .social span { width: 14px; height: 14px; border-radius: 50%; background: var(--ink); display: block; }

  .main-nav {
    position: absolute; left: 54px; top: 111px; width: 789px; height: 30px;
    background: var(--navy); display: flex; padding-left: 18px;
  }
  .main-nav a {
    color: var(--white); text-decoration: none; font-size: 8px; font-weight: 600;
    letter-spacing: .4px; line-height: 30px; padding: 0 22px;
  }
  .main-nav a.current { background: var(--navy-light); }

  .hero {
    position: absolute; left: 54px; top: 165px; width: 789px; height: 360px;
    border: 6px solid #ececec;
    background: linear-gradient(100deg, #f4f5f6 0%, #e9ebed 40%, #dcdfe2 62%, #d8b9a4 80%, #c9a78c 100%);
  }
  .hero-copy { position: absolute; left: 30px; top: 100px; width: 420px; }
  .hero-copy h1 { font-size: 22px; font-weight: 700; color: var(--navy); line-height: 1.25; letter-spacing: .3px; margin-bottom: 12px; }
  .hero-copy p { font-size: 11px; line-height: 1.5; color: var(--ink); width: 330px; margin-bottom: 18px; }
  .btn {
    display: inline-block; background: var(--navy); color: var(--white); font-size: 7.5px;
    font-weight: 600; letter-spacing: .5px; padding: 7px 14px; text-decoration: none;
  }
  .slider-dots { position: absolute; top: 543px; left: 0; width: 898px; display: flex; justify-content: center; gap: 5px; }
  .slider-dots span { width: 6px; height: 6px; border-radius: 50%; background: #bbb; }
  .slider-dots span.active { background: var(--navy); }

  .welcome { position: absolute; top: 570px; left: 54px; width: 789px; text-align: center; }
  .section-title { font-size: 25px; font-weight: 700; letter-spacing: 1px; color: var(--ink); }
  .section-title em { font-style: normal; color: var(--accent); }
  .welcome p { font-size: 7.5px; line-height: 1.7; color: var(--muted); margin: 18px auto 18px; width: 780px; }
  .divider { position: absolute; top: 775px; left: 54px; width: 789px; border-top: 1px solid var(--rule); }

  .services { position: absolute; top: 818px; left: 54px; width: 789px; text-align: center; }
  .service-grid { display: flex; justify-content: space-between; margin-top: 14px; }
  .service { width: 240px; }
  .service-photo { height: 145px; }
  .service h3 { font-size: 10px; font-weight: 700; color: var(--navy); letter-spacing: .5px; margin: 12px 0 5px; }
  .service p { font-size: 7.5px; line-height: 1.6; color: var(--muted); }

  .site-footer {
    position: absolute; top: 1146px; left: 0; width: 898px; height: 54px; background: var(--footer);
    display: flex; align-items: center; justify-content: space-between; padding: 0 54px;
  }
  .site-footer small { color: #cfcfcf; font-size: 7px; }
  .site-footer .social span { background: var(--white); width: 15px; height: 15px; }
</style>
</head>
<body>
  <header class="site-header">
    <div class="brand">Brightcomb</div>
    <div class="follow">
      <div class="follow-label">FOLLOW US</div>
      <div class="social"><span></span><span></span><span></span><span></span><span></span></div>
    </div>
  </header>

  <nav class="main-nav">
    <a class="current" href="#">HOME</a>
    <a href="#">ABOUT US</a>
    <a href="#">GALLERY</a>
    <a href="#">SERVICES</a>
    <a href="#">CONTACT US</a>
  </nav>

  <section class="hero" role="img" aria-label="Smiling bride with styled hair and veil">
    <div class="hero-copy">
      <h1>WE ARE WEDDING HAIR AND<br>MAKEUP COMPANY</h1>
      <p>Neque porro quisquam est qui dolorem ipsum quia dolor sit amet, consectetur, adipisci velit.</p>
      <a class="btn" href="#">LEARN MORE</a>
    </div>
  </section>
  <div class="slider-dots"><span class="active"></span><span></span></div>

  <section class="welcome">
    <h2 class="section-title">WELCOME TO OUR <em>SITE</em></h2>
    <p>Sed ut perspiciatis unde omnis iste natus error sit voluptatem accusantium doloremque laudantium, totam rem aperiam, eaque ipsa quae ab illo inventore veritatis et quasi architecto beatae vitae dicta sunt explicabo. Nemo enim ipsam voluptatem quia voluptas sit aspernatur aut odit aut fugit sed quia consequuntur magni dolores eos qui ratione voluptatem sequi nesciunt.</p>
    <a class="btn" href="#">LEARN MORE</a>
  </section>
  <div class="divider"></div>

  <section class="services">
    <h2 class="section-title">OUR <em>SERVICES</em></h2>
    <div class="service-grid">
      <article class="service">
        <div class="service-photo" role="img" aria-label="Woman with long styled hair" style="background:linear-gradient(135deg,#8a5a3c,#c9a064 55%,#b7c34a);"></div>
        <h3>BONORUM ETMAL</h3>
        <p>Nemo enim ipsam voluptatem quia voluptas sit aspernatur aut odit aut fugit sed quia consequuntur magni.</p>
      </article>
      <article class="service">
        <div class="service-photo" role="img" aria-label="Woman with an elegant updo" style="background:linear-gradient(135deg,#e7e2dc,#c89a86 55%,#6b4a3c);"></div>
        <h3>VOLUPTATEM</h3>
        <p>Nemo enim ipsam voluptatem quia voluptas sit aspernatur aut odit aut fugit sed quia consequuntur magni.</p>
      </article>
      <article class="service">
        <div class="service-photo" role="img" aria-label="Woman in towel receiving a facial treatment" style="background:linear-gradient(135deg,#b9c7d2,#e8dcd4 55%,#cdb7a8);"></div>
        <h3>DOLOREMQUE</h3>
        <p>Nemo enim ipsam voluptatem quia voluptas sit aspernatur aut odit aut fugit sed quia consequuntur magni.</p>
      </article>
    </div>
  </section>

  <footer class="site-footer">
    <small>Copyright ©2013, Brightcomb. All Right Reserved.</small>
    <div class="social"><span></span><span></span><span></span><span></span><span></span></div>
  </footer>
</body>
</html>
```